BLS Business Card 2018

Larkmere Chiropractic. We have two locations that we want to advertise on the same card. Brightvale OrthoCore campus address: 3815 Pellham Dr., Suite 240, Flowood, MS 39417. Madison address: 246 Willowmere Dr., Building D., Madison, MS 39284. website: www.drlarkmere-example.com. o:(601)555-0147 f:(601)555-0183

Target Market(s)

Health care decision makers: primary care doctors and mothers

Contact Information for Business Card

I have no idea; up for any suggestions and I'd do much better picking from examples versus describing what I'm looking for. We are in a very high end location and would like the cards to look really sharp.

Requirements
Must have
• My name, Martin R Belvane, D.C.

```html
<!DOCTYPE html>
<html lang="en">
<head>
<meta charset="utf-8">
<title>Larkmere Chiropractic Business Card</title>
<link href="https://fonts.googleapis.com/css2?family=Cinzel:wght@400&family=Open+Sans:wght@400;700&display=swap" rel="stylesheet">
<style>
  :root {
    --ink: #0b0b0b;
    --paper: #ffffff;
    --stage: #d9d9d9;
    --muted: #e6e6e6;
    --rule: #555555;
  }
  * { margin: 0; padding: 0; box-sizing: border-box; }
  html, body { width: 1200px; height: 782px; overflow: hidden; }
  body {
    background: var(--stage);
    display: flex;
    align-items: center;
    justify-content: center;
    gap: 40px;
    font-family: "Open Sans", Arial, sans-serif;
  }
  .card {
    width: 540px;
    height: 309px;
    position: relative;
    overflow: hidden;
    box-shadow: 0 6px 18px rgba(0,0,0,0.25);
  }
  .card--front {
    background: var(--ink);
    display: flex;
    align-items: center;
    justify-content: center;
  }
  .brand {
    display: flex;
    align-items: center;
    gap: 14px;
    font-family: "Cinzel", Georgia, serif;
    font-weight: 400;
    line-height: 1;
  }
  .brand__mark { width: 14px; height: 14px; border-radius: 50%; }
  .brand__name { display: flex; flex-direction: column; gap: 6px; font-size: 30px; letter-spacing: 1px; }
  .card--front .brand { color: var(--paper); }
  .card--front .brand__mark { background: var(--paper); }

  .card--back { background: var(--ink); }
  .back__top {
    height: 142px;
    background: var(--paper);
    display: flex;
    align-items: flex-end;
    justify-content: center;
    padding-bottom: 18px;
  }
  .card--back .brand { color: var(--ink); }
  .card--back .brand__mark { background: var(--ink); }
  .back__body { color: var(--muted); padding: 14px 26px 0; position: relative; height: 167px; }
  .doctor { font-weight: 700; font-size: 12.5px; text-transform: uppercase; letter-spacing: 0.3px; }
  .rule { border: 0; border-top: 1px solid var(--rule); margin: 6px 0 8px; }
  .locations { display: flex; justify-content: space-between; }
  .location { font-size: 11px; line-height: 1.4; }
  .location__title { font-weight: 700; text-transform: uppercase; font-size: 11px; }
  .location--madison { text-align: right; align-self: flex-end; margin-top: 30px; }
  .contact {
    position: absolute; left: 26px; right: 26px; bottom: 14px;
    font-size: 11px; border-top: 1px solid var(--rule); padding-top: 8px;
  }
</style>
</head>
<body>
  <section class="card card--front">
    <div class="brand">
      <span class="brand__mark"></span>
      <span class="brand__name"><span>Larkmere</span><span>Chiropractic</span></span>
    </div>
  </section>

  <section class="card card--back">
    <div class="back__top">
      <div class="brand">
        <span class="brand__mark"></span>
        <span class="brand__name"><span>Larkmere</span><span>Chiropractic</span></span>
      </div>
    </div>
    <div class="back__body">
      <p class="doctor">Martin R Belvane, D.C.</p>
      <hr class="rule">
      <div class="locations">
        <div class="location">
          <p class="location__title">Brightvale OrthoCore Campus</p>
          <p>3815 Pellham Dr., Suite 240</p>
          <p>Flowood, MS 39417</p>
        </div>
        <div class="location location--madison">
          <p class="location__title">Madison</p>
          <p>246 Willowmere Dr., Building D.</p>
          <p>Madison, MS 39284</p>
        </div>
      </div>
      <p class="contact">P: (601)555-0147 | F: (601)555-0183 | www.drlarkmere-example.com</p>
    </div>
  </section>
</body>
</html>
```